Business Name: K&M Group Cleaning Services - Cleaning business

We need a website to be able to get our services out to the market..
We have just invested over $60,000 in our new van which is capable of doing specialised cleaning services see attached flyer... I will also send through our company logo....We do all types of cleaning from move out cleans, office cleans and have the capability fire flood and restoration services as well
On the flyer it has Desmond as a contact do not use his name only use Glenn as a contact
Want some good pictures included
Prefer people to contact me via email rather than calling me.

```html
<!DOCTYPE html>
<html lang="en">
<head>
<meta charset="utf-8">
<title>K&amp;M Group Cleaning Services</title>
<link rel="stylesheet" href="https://fonts.googleapis.com/css2?family=Montserrat:wght@400;500;600;700&family=Open+Sans:wght@400;600;700&display=swap">
<style>
:root{
  --orange:#ef6a24;
  --orange-dark:#e05a14;
  --ink:#1c1c1c;
  --body:#555;
  --muted:#888;
  --line:#c9c9c9;
  --white:#fff;
  --dark-band:#2a2622;
  --blue:#1a7fd0;
}
*{box-sizing:border-box;margin:0;padding:0}
html,body{width:1200px;height:3974px;overflow:hidden;background:var(--white)}
body{position:relative;font-family:"Open Sans",Arial,sans-serif;color:var(--body)}
.abs{position:absolute}
.heading{font-family:"Montserrat",Arial,sans-serif;color:var(--ink);font-weight:600;letter-spacing:1px}

/* header */
.topbar{top:20px;right:112px;font-size:15px;color:var(--ink);display:flex;gap:14px;align-items:center}
.topbar .sep{color:#999}
.topbar svg{vertical-align:-2px;margin-right:6px}
.nav{top:68px;left:416px;display:flex;font-family:"Montserrat",Arial,sans-serif;font-size:15px;font-weight:600;color:var(--ink)}
.nav span{position:absolute;white-space:nowrap}
.nav .active{color:var(--orange)}
.brand{top:0;left:107px;width:210px;height:210px;border-radius:50%;background:var(--white);z-index:5;display:flex;flex-direction:column;align-items:center;justify-content:center;padding-top:40px}
.brand-dot{width:46px;height:46px;border-radius:50%;background:var(--orange);margin-bottom:14px}
.brand-name{font-family:"Montserrat",Arial,sans-serif;font-weight:600;font-size:22px;color:var(--ink);letter-spacing:2px}

/* hero */
.hero{top:106px;left:0;width:1200px;height:640px;background:linear-gradient(90deg,#3b4a35 0%,#5d6f52 35%,#8d957f 60%,#c9ccc1 80%,#6b6c62 100%)}
.hero-shade{top:106px;left:0;width:700px;height:600px;background:linear-gradient(90deg,rgba(0,0,0,.35),rgba(0,0,0,0))}
.hero-title{top:290px;left:111px;font-family:"Montserrat",Arial,sans-serif;font-weight:700;font-size:48px;color:var(--white);letter-spacing:1px;white-space:nowrap}
.hero-text{top:378px;left:111px;width:560px;font-size:21px;line-height:38px;font-weight:600;color:var(--white)}
.btn-solid{background:var(--orange);color:var(--white);font-family:"Montserrat",Arial,sans-serif;font-weight:700;border-radius:32px;display:flex;align-items:center;justify-content:center}
.hero-btn{top:530px;left:111px;width:193px;height:64px;font-size:18px}
.dots{top:639px;left:562px;display:flex;gap:6px}
.dots i{width:13px;height:13px;border-radius:50%;border:2px solid var(--white)}
.dots i:first-child{background:var(--white)}

/* welcome */
.welcome-title{top:835px;left:111px;font-size:40px;line-height:56px;white-space:nowrap}
.welcome-text{top:965px;left:111px;width:470px;font-size:14.5px;line-height:29px}
.btn-outline{border:2px solid var(--orange);color:var(--orange);border-radius:30px;font-family:"Montserrat",Arial,sans-serif;font-weight:700;display:flex;align-items:center;justify-content:center}
.welcome-btn{top:1177px;left:111px;width:154px;height:50px;font-size:14px}
.video{top:845px;left:638px;width:450px;height:308px;border:4px solid #e4e4e4;background:linear-gradient(135deg,#d9dcdf 0%,#9ea3a8 45%,#3f4a44 70%,#e5e7e8 100%)}
.play{position:absolute;top:50%;left:50%;width:64px;height:64px;margin:-32px 0 0 -32px;border-radius:50%;background:rgba(20,20,20,.85)}

/* specialise */
.special-title{top:1410px;width:1200px;text-align:center;font-size:40px;color:var(--white);font-family:"Montserrat",Arial,sans-serif;font-weight:500;letter-spacing:1px}
.service{top:1507px;width:300px;margin-left:-150px;text-align:center}
.service .photo{width:234px;height:234px;margin:0 auto;border-radius:50%;border:4px solid var(--white)}
.service p{margin-top:18px;font-family:"Montserrat",Arial,sans-serif;font-size:20px;line-height:30px;color:var(--white);font-weight:500;white-space:nowrap}

/* blog */
.blog-title{top:2015px;width:1200px;text-align:center;font-size:40px}
.card{top:2115px;width:310px}
.card .photo{height:218px;border:3px solid #e4e4e4}
.card h3{margin-top:30px;font-family:"Montserrat",Arial,sans-serif;font-weight:600;font-size:24px;color:var(--ink);white-space:nowrap}
.meta{margin-top:12px;font-size:13.5px;color:#444;display:flex;align-items:center;gap:6px}
.meta .bar{margin:0 8px}
.card .excerpt{margin-top:22px;font-size:13.5px;line-height:28px;color:#666}
.card .more{margin-top:24px;font-family:"Montserrat",Arial,sans-serif;font-weight:700;font-size:14px;color:var(--orange)}

/* high pressure */
.hp-text{top:2760px;left:615px;width:480px;color:var(--white)}
.hp-text h2{font-family:"Montserrat",Arial,sans-serif;font-weight:500;font-size:42px;line-height:56px;letter-spacing:1px;white-space:nowrap}
.hp-text p{margin-top:24px;font-size:14.5px;line-height:29px;color:#eee}
.hp-btn{top:3134px;left:615px;width:154px;height:50px;font-size:14px;border-color:var(--white);color:var(--white)}
.badge{top:3014px;left:350px;width:174px;height:174px;border-radius:50%;background:var(--blue);border:4px solid #fff;display:flex;align-items:center;justify-content:center;text-align:center;color:var(--white);font-family:"Montserrat",Arial,sans-serif;font-weight:700;font-size:23px;line-height:28px}

/* contact */
.contact-title{top:3378px;width:1200px;text-align:center;font-size:40px}
.sub{font-family:"Montserrat",Arial,sans-serif;font-weight:500;font-size:18px;color:var(--ink)}
.field{border:1.5px solid #bbb;border-radius:6px;font-size:13.5px;color:#555;padding:10px 16px}
.submit{top:3774px;left:617px;width:96px;height:42px;font-size:14px;border-radius:22px}
.info-row{left:776px;display:flex;align-items:flex-start;gap:18px;font-size:13.5px;line-height:24px;color:#555}
.info-icon{width:36px;height:36px;border-radius:50%;border:1.5px solid #ddd;display:flex;align-items:center;justify-content:center;flex:none}
.social{top:3779px;left:776px;display:flex;gap:10px}
.social i{width:36px;height:36px;border-radius:50%;border:1.5px solid var(--orange);display:block}
.footer-line{top:3868px;left:111px;width:976px;height:1px;background:var(--line)}
.copyright{top:3906px;width:1200px;text-align:center;font-size:13px;color:#555}
</style>
</head>
<body>

<!-- header -->
<div class="abs topbar">
  <span><svg width="14" height="14" viewBox="0 0 24 24"><path fill="#ef6a24" d="M6.6 10.8a15.1 15.1 0 0 0 6.6 6.6l2.2-2.2c.3-.3.7-.4 1-.2 1.1.4 2.3.6 3.6.6.6 0 1 .4 1 1V20c0 .6-.4 1-1 1A17 17 0 0 1 3 4c0-.6.4-1 1-1h3.5c.6 0 1 .4 1 1 0 1.3.2 2.5.6 3.6.1.3 0 .7-.2 1z"/></svg>0400 555 019</span>
  <span class="sep">|</span>
  <span><svg width="15" height="12" viewBox="0 0 24 18"><rect width="24" height="18" rx="2" fill="#ef6a24"/><path d="M2 2l10 8 10-8" stroke="#fff" stroke-width="2" fill="none"/></svg>hello@kmgroupcleaning.example</span>
</div>
<nav class="abs nav">
  <span class="active" style="left:0">HOME</span>
  <span style="left:84px">ABOUT US</span>
  <span style="left:199px">SERVICES</span>
  <span style="left:310px">BLOG</span>
  <span style="left:390px">RESOURCES</span>
  <span style="left:519px">CONTACT US</span>
  <span style="left:658px"><svg width="16" height="16" viewBox="0 0 24 24"><circle cx="10" cy="10" r="7" stroke="#1c1c1c" stroke-width="3" fill="none"/><path d="M15 15l7 7" stroke="#1c1c1c" stroke-width="3"/></svg></span>
</nav>
<div class="abs brand">
  <div class="brand-dot"></div>
  <div class="brand-name">K&amp;M GROUP</div>
</div>

<!-- hero -->
<div class="abs hero" role="img" aria-label="Worker pressure cleaning a paved outdoor area"></div>
<div class="abs hero-shade"></div>
<svg class="abs" style="top:600px;left:0" width="1200" height="160" viewBox="0 0 1200 160">
  <path d="M0 30 Q600 200 1200 30 L1200 160 L0 160 Z" fill="#fff"/>
  <path d="M0 50 Q600 215 1200 50" stroke="#ef6a24" stroke-width="5" fill="none"/>
</svg>
<h1 class="abs hero-title">K&amp;M GROUP CLEANING</h1>
<p class="abs hero-text">We do all types of cleaning from move out cleans, office cleans and have the capability fire flood and restoration services as well.</p>
<div class="abs btn-solid hero-btn">BOOK NOW!</div>
<div class="abs dots"><i></i><i></i><i></i><i></i></div>

<!-- welcome -->
<h2 class="abs heading welcome-title">WELCOME TO<br>K&amp;M GROUP CLEANING</h2>
<p class="abs welcome-text">Our professional Titan 900 Truckmount unit, is one of the most powerful slide-in on the market. This unit has more heat, more vacuum power and more pressure for a superior clean! Triple-source heat and a high-pressure solution pump makes it perfect for hard surface cleaning using higher pressure which is ideal for both large commercial and residential jobs.</p>
<div class="abs btn-outline welcome-btn">READ MORE</div>
<div class="abs video" role="img" aria-label="Video of the truckmount cleaning unit inside the company van">
  <div class="play"><svg width="64" height="64" viewBox="0 0 64 64"><path d="M26 20l18 12-18 12z" fill="#fff"/></svg></div>
</div>

<!-- specialise band -->
<svg class="abs" style="top:1290px;left:0" width="1200" height="630" viewBox="0 0 1200 630">
  <path d="M0 60 Q600 -40 1200 60" stroke="#222" stroke-width="6" fill="none"/>
  <path d="M0 100 Q600 0 1200 100 L1200 510 Q600 610 0 510 Z" fill="#ef6a24"/>
  <path d="M0 550 Q600 650 1200 550" stroke="#222" stroke-width="6" fill="none"/>
  <path d="M62 312 l-12 12 l12 12" stroke="#fff" stroke-width="4" fill="none"/>
  <path d="M1138 312 l12 12 l-12 12" stroke="#fff" stroke-width="4" fill="none"/>
</svg>
<h2 class="abs special-title">WE SPECIALISE IN</h2>
<div class="abs service" style="left:228px"><div class="photo" role="img" aria-label="Tile and grout cleaning machine on a tiled floor" style="background:linear-gradient(135deg,#e8e8e8,#9fb6d8 50%,#3d5ea8)"></div><p>Tile and<br>grout clean</p></div>
<div class="abs service" style="left:474px"><div class="photo" role="img" aria-label="Vacuum cleaning a carpet" style="background:linear-gradient(135deg,#f2f2f2,#c9c9c9 50%,#6d6d6d)"></div><p>Commercial &amp; residential<br>carpet cleaning</p></div>
<div class="abs service" style="left:723px"><div class="photo" role="img" aria-label="Roof gutter filled with leaves" style="background:linear-gradient(135deg,#5a4030,#b59a7c 50%,#e4ddd2)"></div><p>Gutter<br>cleaning</p></div>
<div class="abs service" style="left:970px"><div class="photo" role="img" aria-label="Air mover drying a wet floor" style="background:linear-gradient(135deg,#efe9e0,#c9b9a2 50%,#2b6ab8)"></div><p>Fire and flood<br>restoration capability</p></div>

<!-- blog -->
<h2 class="abs heading blog-title">LATEST BLOG</h2>
<article class="abs card" style="left:111px">
  <div class="photo" role="img" aria-label="Cleaners mopping an office floor" style="background:linear-gradient(135deg,#d8d8d0,#7c8a6a 50%,#2c3a2a)"></div>
  <h3>Finibus Bonoet Malorum</h3>
  <div class="meta"><svg width="12" height="12" viewBox="0 0 12 12"><rect x="1" y="2" width="10" height="9" rx="1" fill="#ef6a24"/></svg>04/04/2019<span class="bar">|</span><svg width="12" height="12" viewBox="0 0 12 12"><circle cx="6" cy="4" r="3" fill="#ef6a24"/><path d="M1 12a5 5 0 0 1 10 0z" fill="#ef6a24"/></svg>Glenn</div>
  <p class="excerpt">Nam libero tempore, cum soluta nobis est eligendi optio cumque nihil impedit quo minus id quod maxime placeat facere.</p>
  <p class="more">READ MORE</p>
</article>
<article class="abs card" style="left:445px">
  <div class="photo" role="img" aria-label="Worker pressure washing a brick wall" style="background:linear-gradient(135deg,#eeeae2,#b9b3a6 50%,#6f8a5a)"></div>
  <h3>Finibus Bonoet Malorum</h3>
  <div class="meta"><svg width="12" height="12" viewBox="0 0 12 12"><rect x="1" y="2" width="10" height="9" rx="1" fill="#ef6a24"/></svg>04/04/2019<span class="bar">|</span><svg width="12" height="12" viewBox="0 0 12 12"><circle cx="6" cy="4" r="3" fill="#ef6a24"/><path d="M1 12a5 5 0 0 1 10 0z" fill="#ef6a24"/></svg>Glenn</div>
  <p class="excerpt">Nam libero tempore, cum soluta nobis est eligendi optio cumque nihil impedit quo minus id quod maxime placeat facere.</p>
  <p class="more">READ MORE</p>
</article>
<article class="abs card" style="left:776px">
  <div class="photo" role="img" aria-label="Gloved hand clearing leaves from a gutter" style="background:linear-gradient(135deg,#6f7f4a,#8a6a45 50%,#d8d4c8)"></div>
  <h3>Finibus Bonoet Malorum</h3>
  <div class="meta"><svg width="12" height="12" viewBox="0 0 12 12"><rect x="1" y="2" width="10" height="9" rx="1" fill="#ef6a24"/></svg>04/04/2019<span class="bar">|</span><svg width="12" height="12" viewBox="0 0 12 12"><circle cx="6" cy="4" r="3" fill="#ef6a24"/><path d="M1 12a5 5 0 0 1 10 0z" fill="#ef6a24"/></svg>Glenn</div>
  <p class="excerpt">Nam libero tempore, cum soluta nobis est eligendi optio cumque nihil impedit quo minus id quod maxime placeat facere.</p>
  <p class="more">READ MORE</p>
</article>

<!-- high pressure band -->
<svg class="abs" style="top:2640px;left:0" width="1200" height="660" viewBox="0 0 1200 660">
  <defs>
    <linearGradient id="hpBg" x1="0" y1="0" x2="1" y2="1">
      <stop offset="0" stop-color="#4a4038"/>
      <stop offset=".5" stop-color="#2e2822"/>
      <stop offset="1" stop-color="#6b5a48"/>
    </linearGradient>
  </defs>
  <path d="M0 95 Q600 -45 1200 95" stroke="#ef6a24" stroke-width="6" fill="none"/>
  <path d="M0 110 Q600 -25 1200 110 L1200 565 Q600 690 0 565 Z" fill="url(#hpBg)" role="img" aria-label="High pressure cleaning a timber deck"/>
  <path d="M0 580 Q600 705 1200 580" stroke="#ef6a24" stroke-width="6" fill="none"/>
</svg>
<div class="abs" role="img" aria-label="Truckmount pressure cleaning machine" style="top:2760px;left:185px;width:340px;height:330px;background:linear-gradient(160deg,#3aa845,#7bcf4a 45%,#9a9ea2 80%);border-radius:6px"></div>
<div class="abs badge">Delivering<br>Hot Water<br>at 2500 psi!</div>
<div class="abs hp-text">
  <h2>HIGH PRESSURE<br>CLEANING SERVICES</h2>
  <p>Whether you need to clean your existing premises or even remove graffiti, our commercial cleaning solutions go above and beyond when it comes to restoring your premises.</p>
  <p>We have extensive experience and work closely with Councils, Recreational Parks, Real Estate Agents, Community Housing Providers, High-profile retail shops and more.</p>
</div>
<div class="abs btn-outline hp-btn">READ MORE</div>

<!-- contact -->
<h2 class="abs heading contact-title">CONTACT US</h2>
<h3 class="abs sub" style="top:3490px;left:111px">Contact form</h3>
<div class="abs field" style="top:3551px;left:111px;width:297px;height:42px">Name :</div>
<div class="abs field" style="top:3551px;left:419px;width:294px;height:42px">Phone no :</div>
<div class="abs field" style="top:3609px;left:111px;width:602px;height:45px">Email :</div>
<div class="abs field" style="top:3670px;left:111px;width:602px;height:85px">Message :</div>
<div class="abs btn-solid submit">SUBMIT</div>

<h3 class="abs sub" style="top:3490px;left:776px">Contact Information</h3>
<div class="abs info-row" style="top:3546px">
  <span class="info-icon"><svg width="14" height="16" viewBox="0 0 14 18"><path d="M7 0a7 7 0 0 0-7 7c0 5 7 11 7 11s7-6 7-11a7 7 0 0 0-7-7z" fill="#ef6a24"/><circle cx="7" cy="7" r="2.5" fill="#fff"/></svg></span>
  <span>27 Harlow Court Brookvale<br>Park 3110</span>
</div>
<div class="abs info-row" style="top:3615px">
  <span class="info-icon"><svg width="14" height="14" viewBox="0 0 24 24"><path fill="#ef6a24" d="M6.6 10.8a15.1 15.1 0 0 0 6.6 6.6l2.2-2.2c.3-.3.7-.4 1-.2 1.1.4 2.3.6 3.6.6.6 0 1 .4 1 1V20c0 .6-.4 1-1 1A17 17 0 0 1 3 4c0-.6.4-1 1-1h3.5c.6 0 1 .4 1 1 0 1.3.2 2.5.6 3.6.1.3 0 .7-.2 1z"/></svg></span>
  <span style="line-height:36px">0400 555 019</span>
</div>
<div class="abs info-row" style="top:3679px">
  <span class="info-icon"><svg width="15" height="12" viewBox="0 0 24 18"><rect width="24" height="18" rx="2" fill="#ef6a24"/><path d="M2 2l10 8 10-8" stroke="#fff" stroke-width="2" fill="none"/></svg></span>
  <span style="line-height:36px">hello@kmgroupcleaning.example</span>
</div>
<h3 class="abs sub" style="top:3740px;left:776px">Social Media</h3>
<div class="abs social" aria-label="Social media links"><i></i><i></i><i></i></div>

<div class="abs footer-line"></div>
<p class="abs copyright">Copyright © 2019, K&amp;M Group. All rights reserved.</p>
<svg class="abs" style="top:3904px;left:1062px" width="24" height="14" viewBox="0 0 24 14"><path d="M2 12L12 2l10 10" stroke="#999" stroke-width="2.5" fill="none"/></svg>

</body>
</html>
```